Lark Vista Perks Needs a Website Design

We need a website design for a new service we are starting. Users enter a coupon in a redemption page and either create an account or sign in. they can then use the credits they accumulate from the coupons to purchase items listed on the site.

we need a design for the following:
-the coupon redemption page (with a choice to either sign in or create an account)
-a product listing page (with search filters and a search bar. the search bar can be displayed in the header of the site)
-a product detail page, showing the product's title, image, credit redemption value, brand and any category associated with the item
-a my account page, with:
*a list of the pluses (coupons/credit added to account) and the minuses (orders placed/credits subtracted from account) to show a detailed description of their history on the site)
*an area for users to edit their name, phone number, address etc
*an area for users to add / edit their casino membership number and casino
*an area for users to add a coupon to their account
-a cart / checkout process:
*cart displaying items and their total
*entering / selecting an address from their account
*review order details page where they can submit their order (and warning the user that doing so will subtract the required credits from their account)

remember that no ecommerce or money is used on the site.. users are spending their credits and checkout their cart with the credits they accumulated, so the items each have a credit redemption value and the checkout process is shown in credits.

we are not very particular with any design preference, other than we'd like it to be predominately white.

If designing the site with css please make sure to use bootstrap in your designs. thanks!

Target Market(s)

adults 45-65

Industry/Entity Type

Casino

Coding

Coded - Design and coding required

Number of Pages Required

5+ page

Font styles to use
Sans Serif

Requirements
Must have
• css must use with bootstrap
Nice to have
• simplified, easy interface. we are targeting an older crowd and dont want to confuse them
Should not have
• the site shouldnt have any dollar values. all product prices, checkout totals and user accrual's (in the my account page) should be in credits

```html
<!DOCTYPE html>
<html lang="en">
<head>
<meta charset="utf-8">
<title>Lark Vista Perks</title>
<link href="https://fonts.googleapis.com/css2?family=Open+Sans:wght@400;600;700;800&display=swap" rel="stylesheet">
<style>
:root{
  --blue:#1f6fce;
  --green:#6fb324;
  --green-dark:#5e9e1a;
  --text:#444;
  --muted:#777;
  --line:#e3e3e3;
  --footer:#3e3e3e;
  --footer-bottom:#333;
  --white:#fff;
}
*{box-sizing:border-box;margin:0;padding:0}
html,body{width:723px;height:1200px;overflow:hidden;background:var(--white);font-family:'Open Sans',sans-serif;color:var(--text)}
.page{position:relative;width:723px;height:1200px}
.btn{display:inline-block;background:var(--green);color:var(--white);font-weight:700;font-size:9px;border-radius:1px;text-align:center}

/* header */
.site-header{position:absolute;top:0;left:0;width:723px;height:60px}
.brand{position:absolute;left:46px;top:19px;font-size:18px;font-weight:700;color:var(--blue);letter-spacing:.2px}
.brand span{color:var(--green)}
.search{position:absolute;left:228px;top:17px;width:275px;height:26px;border:1px solid #ddd;display:flex;font-size:8.5px;color:#888}
.search .filter{width:66px;border-right:1px solid #ddd;display:flex;align-items:center;justify-content:center;gap:5px}
.search .field{flex:1;display:flex;align-items:center;padding-left:8px}
.search .go{width:27px;background:var(--blue);display:flex;align-items:center;justify-content:center}
.account{position:absolute;left:539px;top:9px;width:61px;height:18px;line-height:18px;font-size:8px}
.cart{position:absolute;left:616px;top:12px;font-size:8.5px;font-weight:700;color:var(--blue);display:flex;align-items:center;gap:4px}
.cart b{color:var(--green)}
.top-nav{position:absolute;top:38px;left:534px;font-size:8.5px;font-weight:600;color:#555;display:flex;gap:19px}

/* hero */
.hero{position:absolute;top:60px;left:0;width:723px;height:273px;background:linear-gradient(100deg,#b28a48 0%,#8c7656 35%,#5f5a55 60%,#cfcbc6 78%,#9b8f80 100%)}
.hero-copy{position:absolute;left:46px;top:78px;color:var(--white)}
.hero-copy h1{font-size:31px;font-weight:800;letter-spacing:1px;line-height:1}
.hero-copy h2{font-size:18.5px;font-weight:800;letter-spacing:.8px;line-height:1.15;margin-top:10px}
.hero-copy .btn{margin-top:20px;width:72px;height:22px;line-height:22px}
.dots{position:absolute;left:46px;top:208px;display:flex;gap:5px}
.dots i{width:7px;height:7px;background:var(--white);border-radius:1px}
.dots i:first-child{background:var(--blue)}

/* sections */
.section-title{position:absolute;left:0;width:723px;text-align:center;font-size:16px;font-weight:600;color:#444;letter-spacing:.3px}
.rule{position:absolute;left:46px;width:632px;height:1px;background:var(--line)}
.arrow{position:absolute;width:10px;height:16px}
.row{position:absolute;left:46px;width:632px;display:flex;justify-content:space-between}
.card{border:1px solid #ddd;background:var(--white);text-align:center}

.coupon{width:144px;height:140px;padding:12px 12px 0}
.coupon .art{height:48px;margin:0 auto}
.coupon p{font-size:8.5px;margin-top:15px;line-height:1.4}
.coupon p b{color:var(--blue);font-weight:600}
.coupon p b.strong{font-weight:700}
.card .btn{width:72px;height:21px;line-height:21px;margin-top:10px}

.product{width:144px;height:202px;padding:12px 12px 0}
.product .art{height:100px;width:90px;margin:0 auto}
.product h3{font-size:10px;font-weight:700;color:var(--blue);margin-top:14px}
.product dl{display:flex;justify-content:space-between;font-size:8px;text-align:left;margin-top:10px;line-height:1.4;padding:0 1px}
.product dl dd{font-weight:400}
.product dl div:last-child{text-align:left}

.brand-box{width:145px;height:47px;border:1px solid #ddd;display:flex;align-items:center;justify-content:center;gap:6px;font-size:16px;font-weight:600;color:#333}
.brand-box i{width:14px;height:14px;border-radius:50%}

/* footer */
.site-footer{position:absolute;top:1002px;left:0;width:723px;height:144px;background:var(--footer);color:#cfcfcf}
.fcol{position:absolute;top:30px}
.fcol h4{font-size:10px;font-weight:700;color:var(--white);letter-spacing:.4px;margin-bottom:9px}
.fcol p{font-size:8px;line-height:15.5px;width:195px}
.fcol a{display:block;font-size:8px;line-height:20px;color:#cfcfcf;text-decoration:none}
.fcol .more{color:var(--green);font-weight:700;margin-top:3px}
.newsletter input{width:145px;height:25px;border:none;padding-left:8px;font-family:inherit;font-size:7px;color:#666;display:block}
.newsletter .btn{width:60px;height:21px;line-height:21px;margin:7px 0 0 85px}
.bottom-bar{position:absolute;top:1146px;left:0;width:723px;height:54px;background:var(--footer-bottom);color:#aaa}
.bottom-bar small{position:absolute;left:46px;top:21px;font-size:7px}
.social{position:absolute;right:58px;top:18px;display:flex;gap:11px}
.social i{width:11px;height:11px;border-radius:50%;background:#bbb}
</style>
</head>
<body>
<div class="page">

<header class="site-header">
  <div class="brand">Lark Vista <span>Perks</span></div>
  <div class="search">
    <div class="filter">
      <svg width="7" height="7" viewBox="0 0 10 10"><path d="M0 0h10L6 5v5L4 9V5z" fill="#555"/></svg>Filter
      <svg width="6" height="4" viewBox="0 0 6 4"><path d="M0 0l3 3 3-3" stroke="#555" fill="none"/></svg>
    </div>
    <div class="field">Search..</div>
    <div class="go"><svg width="9" height="9" viewBox="0 0 10 10"><circle cx="4" cy="4" r="3" stroke="#fff" stroke-width="1.5" fill="none"/><path d="M6.3 6.3L9 9" stroke="#fff" stroke-width="1.5"/></svg></div>
  </div>
  <a class="btn account">My Account</a>
  <div class="cart"><svg width="9" height="8" viewBox="0 0 10 9"><path d="M0 0h2l1.5 5h5L10 1H3" fill="none" stroke="#1f6fce" stroke-width="1.4"/><circle cx="4" cy="7.5" r="1" fill="#1f6fce"/><circle cx="8" cy="7.5" r="1" fill="#1f6fce"/></svg>My Cart <b>(0)</b></div>
  <nav class="top-nav"><span>Coupon Redemption</span><span>Products</span></nav>
</header>

<section class="hero" role="img" aria-label="Person using a laptop with a coupon on screen">
  <div class="hero-copy">
    <h1>LARK VISTA PERKS</h1>
    <h2>WE ARE A COUPON<br>REDEMPTION COMPANY.</h2>
    <a class="btn">Read More</a>
  </div>
  <div class="dots"><i></i><i></i><i></i><i></i></div>
</section>

<h2 class="section-title" style="top:363px">Coupon Redemption</h2>
<svg class="arrow" style="left:27px;top:462px" viewBox="0 0 10 16"><path d="M8 1L2 8l6 7" stroke="#bbb" stroke-width="2" fill="none"/></svg>
<svg class="arrow" style="left:687px;top:462px" viewBox="0 0 10 16"><path d="M2 1l6 7-6 7" stroke="#bbb" stroke-width="2" fill="none"/></svg>
<div class="row" style="top:401px">
  <div class="card coupon"><div class="art" role="img" aria-label="Gift voucher artwork" style="width:118px;background:linear-gradient(90deg,#f4f1ec 70%,#c8232c 70%)"></div><p>Earn upto<br><b>8 Points</b> per <b class="strong">100</b> spent</p><a class="btn">Redeem Now</a></div>
  <div class="card coupon"><div class="art" role="img" aria-label="Discount voucher artwork" style="width:111px;background:linear-gradient(90deg,#1d1d1d 50%,#5c7a2e 100%)"></div><p>Earn upto<br><b>8 Points</b> per <b class="strong">100</b> spent</p><a class="btn">Redeem Now</a></div>
  <div class="card coupon"><div class="art" role="img" aria-label="Red gift voucher artwork" style="width:117px;background:#d8392f"></div><p>Earn upto<br><b>8 Points</b> per <b class="strong">100</b> spent</p><a class="btn">Redeem Now</a></div>
  <div class="card coupon"><div class="art" role="img" aria-label="Valentine's day voucher artwork" style="width:92px;height:55px;background:linear-gradient(90deg,#8fd3c2,#f3a9b4 60%,#f6c9cf)"></div><p style="margin-top:8px">Earn upto<br><b>8 Points</b> per <b class="strong">100</b> spent</p><a class="btn">Redeem Now</a></div>
</div>

<div class="rule" style="top:573px"></div>
<h2 class="section-title" style="top:592px">Product Listing</h2>
<svg class="arrow" style="left:27px;top:725px" viewBox="0 0 10 16"><path d="M8 1L2 8l6 7" stroke="#bbb" stroke-width="2" fill="none"/></svg>
<svg class="arrow" style="left:687px;top:725px" viewBox="0 0 10 16"><path d="M2 1l6 7-6 7" stroke="#bbb" stroke-width="2" fill="none"/></svg>
<div class="row" style="top:632px">
  <div class="card product"><div class="art" role="img" aria-label="Orange leather handbag" style="background:radial-gradient(ellipse at 50% 60%,#e2622f 0%,#eac9a4 45%,#fff 72%)"></div><h3>Product Name</h3><dl><div><dt>Item Code:</dt><dd>REW 123</dd></div><div><dt>Point</dt><dd>10800</dd></div></dl><a class="btn">Redeem Now</a></div>
  <div class="card product"><div class="art" role="img" aria-label="Black sunglasses" style="width:114px;background:radial-gradient(ellipse at 50% 50%,#2a2a2a 0%,#777 30%,#fff 55%)"></div><h3>Product Name</h3><dl><div><dt>Item Code:</dt><dd>REW 123</dd></div><div><dt>Point</dt><dd>10800</dd></div></dl><a class="btn">Redeem Now</a></div>
  <div class="card product"><div class="art" role="img" aria-label="Smartphone" style="width:46px;border-radius:7px;background:linear-gradient(180deg,#e8e8e8 8%,#2f6d8f 15%,#2b4f3d 85%,#e8e8e8 92%)"></div><h3>Product Name</h3><dl><div><dt>Item Code:</dt><dd>REW 123</dd></div><div><dt>Point</dt><dd>10800</dd></div></dl><a class="btn">Redeem Now</a></div>
  <div class="card product"><div class="art" role="img" aria-label="Laptop computer" style="width:116px;background:linear-gradient(170deg,#fff 12%,#4a5d8a 20%,#3a8fb7 55%,#b9bcc2 72%,#fff 85%)"></div><h3>Product Name</h3><dl><div><dt>Item Code:</dt><dd>REW 123</dd></div><div><dt>Point</dt><dd>10800</dd></div></dl><a class="btn">Redeem Now</a></div>
</div>

<div class="rule" style="top:862px"></div>
<h2 class="section-title" style="top:881px">Featured Brands</h2>
<div class="row" style="top:919px">
  <div class="brand-box"><i style="background:#f39a1e"></i>Ferrow</div>
  <div class="brand-box"><i style="background:#2b9ad8"></i>Brightmoor</div>
  <div class="brand-box"><i style="background:#f26b21"></i>Tallis</div>
  <div class="brand-box" style="width:123px"><i style="background:#e9471f"></i>Quillan</div>
</div>

<footer class="site-footer">
  <div class="fcol" style="left:46px"><h4>ABOUT US</h4><p>Aliquam molestie, mi et imperdiet euismod, dui purus auctor tellus, et interdum lacus lectus et ante. Sed accumsan sollicitudin sapien, sit amet adipiscing turpis gravida ac.</p><a class="more">Read More</a></div>
  <div class="fcol" style="left:268px"><h4>POLICIES</h4><a>Privacy Policy</a><a>User Account</a><a>Shipment</a><a>Terms and Conditions</a></div>
  <div class="fcol" style="left:414px"><h4>QUICK LINKS</h4><a>Contact Us</a><a>About Us</a><a>Careers</a><a>FAQs</a></div>
  <div class="fcol newsletter" style="left:533px"><h4>SIGN UP NEWSLETTER</h4><input type="text" value="Enter Mail Address" aria-label="Email address"><a class="btn">Sign Up</a></div>
</footer>
<div class="bottom-bar">
  <small>Copyright © 2017. Company Name. All Right Reserved</small>
  <div class="social" aria-label="Social links"><i></i><i></i><i></i><i></i><i></i><i></i></div>
</div>

</div>
</body>
</html>
```